Brenwick Structures Construction Company Seeking Modern Website

We are a small construction company wanting to create a web presence. We don't have much in the way of current content but will get photos as they come in. Attached is a picture of our business card.
The pages we would like on the menu are:
Home
Portfolio
Product Specs
Testimonials
Our Process
Contact
Some designs we like are:
http://www.tovasheds-example.com/
http://www.qrnstructures-example.com/
http://dunholtbarns-example.com/
http://pellingframes-example.com/
Not much requirements other than that so feel free to be creative!
Updates
Target Market(s)
Construction
Commercial and Residential Buildings
Industry/Entity Type
Construction Company
Number of Pages Required
5+ page
Look and feel

```html
<!DOCTYPE html>
<html lang="en">
<head>
<meta charset="utf-8">
<title>Brenwick Structures</title>
<link href="https://fonts.googleapis.com/css2?family=Roboto:wght@300;400;500;700&display=swap" rel="stylesheet">
<style>
:root{
  --blue:#0e9fd8;
  --red:#d6322b;
  --ink:#2b2b2b;
  --body:#555;
  --line:#e6e6e6;
  --soft:#f6f5f5;
  --white:#fff;
  --footer:#363b40;
  --footer-text:#d9dcdf;
}
*{margin:0;padding:0;box-sizing:border-box}
html,body{width:1200px;height:2267px;overflow:hidden}
body{position:relative;background:var(--white);font-family:"Roboto",Arial,sans-serif;color:var(--body)}
.abs{position:absolute}

/* top bar */
.topbar{left:0;top:0;width:1200px;height:45px;border-bottom:1px solid var(--line)}
.topbar .call{left:609px;top:15px;font-size:13px;color:#333;font-weight:500}
.topbar .call b{color:var(--blue);font-size:15px;font-weight:500;margin-left:3px}
.toplinks{left:852px;top:15px;display:flex;font-size:13px;color:#333}
.toplinks span{display:flex;align-items:center;gap:5px;padding:0 14px;border-left:1px solid var(--line)}
.toplinks span:first-child{border-left:0}

/* header */
.header{left:0;top:45px;width:1200px;height:91px}
.brand{left:76px;top:26px;display:flex;align-items:center;gap:10px;font-size:27px;font-weight:700;color:var(--blue)}
.brand i{width:16px;height:16px;border-radius:50%;background:var(--red);display:block}
.nav{left:442px;top:0;display:flex;height:91px;align-items:center;font-size:12.5px;font-weight:500;color:#333;letter-spacing:.3px}
.nav a{padding:0 16px;text-decoration:none;color:inherit;line-height:91px;position:relative}
.nav a.active{color:var(--blue)}
.nav a.active::before{content:"";position:absolute;left:8px;right:8px;top:34px;height:2px;background:var(--blue)}
.contact-btn{left:1005px;top:31px;width:119px;height:33px;background:var(--blue);color:var(--white);font-size:13px;font-weight:500;display:flex;align-items:center;justify-content:center;letter-spacing:.3px}

/* hero */
.hero{left:0;top:136px;width:1200px;height:526px;background:linear-gradient(100deg,#d8e2ea 0%,#eef2f5 45%,#f7f9fb 70%,#dfe6ec 100%)}
.dots{left:1156px;top:166px;display:flex;flex-direction:column;gap:7px}
.dots i{width:13px;height:13px;border-radius:50%;background:var(--white);display:block}
.dots i.on{background:var(--blue)}

/* welcome */
.welcome{left:0;top:662px;width:1200px;height:710px;background:var(--soft)}
.welcome h1{position:absolute;left:0;width:1200px;top:61px;text-align:center;font-weight:400;font-size:29px;color:var(--ink);letter-spacing:.5px}
.welcome h1 span{color:var(--red)}
.welcome .intro{position:absolute;left:163px;width:874px;top:110px;text-align:center;font-size:13.5px;line-height:22px;color:#555}
.tabs{position:absolute;top:214px;left:0;width:1200px;font-size:16px;font-weight:500;color:#222;letter-spacing:.5px}
.tabs span{position:absolute;top:0;height:40px;display:flex;align-items:center;justify-content:center}
.tabs .active{left:328px;width:156px;border:2px solid var(--red);border-radius:4px;color:var(--red)}
.tab-com{left:520px;width:150px}
.tab-agr{left:715px;width:150px}

.card{position:absolute;top:295px;width:241px;height:344px;background:var(--white);border:1px solid #ececec}
.card .photo{height:178px}
.card p{padding:20px 18px 0;text-align:center;font-size:13.5px;line-height:22px;color:#555}
.btn-red,.btn-blue{position:absolute;left:50%;transform:translateX(-50%);height:38px;border:2px solid var(--red);border-radius:4px;color:var(--red);font-size:13.5px;font-weight:500;display:flex;align-items:center;justify-content:center;letter-spacing:.3px}
.btn-red{top:286px;width:133px}
.btn-blue{border-color:var(--blue);color:var(--blue);width:136px}

/* testimonial */
.testimonial{left:0;top:1372px;width:1200px;height:292px;background:linear-gradient(90deg,#5a5753 0%,#6e6a64 40%,#5d5a56 75%,#47464a 100%)}
.quote-mark{left:128px;top:60px}
.testimonial blockquote{position:absolute;left:128px;top:112px;width:772px;font-size:14px;line-height:23px;font-style:italic;color:var(--white);text-align:justify}
.arrows{left:127px;top:206px;display:flex;gap:2px}
.avatar{left:937px;top:60px;width:136px;height:136px;border-radius:50%;border:4px solid #d9d9d9;background:linear-gradient(180deg,#e9ebee,#b7bcc3)}
.person{left:905px;top:208px;width:200px;text-align:center;color:var(--blue);font-size:14px;letter-spacing:.3px}

/* blog */
.blog-title{left:0;top:1716px;width:1200px;text-align:center;font-size:28px;font-weight:400;color:var(--ink);letter-spacing:.5px}
.post{position:absolute;top:1771px;width:331px;height:350px}
.post .photo{height:196px;border-radius:3px;position:relative}
.date{position:absolute;left:21px;top:24px;width:68px;height:64px;background:var(--blue);color:var(--white);text-align:center}
.date b{display:block;font-size:27px;font-weight:500;line-height:32px;margin-top:4px}
.date small{display:block;font-size:12px;line-height:14px}
.date::after{content:"";position:absolute;left:0;bottom:-8px;border-left:10px solid var(--blue);border-bottom:8px solid transparent}
.post p{padding-top:22px;text-align:center;font-size:13.5px;line-height:22px;color:#555}
.post .btn-blue{top:301px}

/* footer */
.footer{left:0;top:2155px;width:1200px;height:112px;background:var(--footer)}
.footer-nav{left:76px;top:34px;display:flex;font-size:13px;color:var(--footer-text);letter-spacing:.3px}
.footer-nav span{padding:0 14px;border-left:1px solid #8a8f94;line-height:13px}
.footer-nav span:first-child{padding-left:0;border-left:0}
.copyright{left:76px;top:64px;font-size:13px;color:var(--footer-text)}
.socials{left:956px;top:39px;display:flex;gap:14px}
.socials i{display:block;width:32px;height:32px;border-radius:2px}
</style>
</head>
<body>

<div class="abs topbar">
  <div class="abs call">CALL US TODAY! <b>555.204.7781</b></div>
  <div class="abs toplinks">
    <span><svg width="11" height="11" viewBox="0 0 11 11"><circle cx="5.5" cy="5.5" r="5.5" fill="#0e9fd8"/></svg>FAQ's</span>
    <span><svg width="13" height="11" viewBox="0 0 13 11"><ellipse cx="6.5" cy="4.5" rx="6.5" ry="4.5" fill="#0e9fd8"/><path d="M2 7 L1 11 L6 8Z" fill="#0e9fd8"/></svg>Testimonials</span>
    <span><svg width="12" height="12" viewBox="0 0 12 12"><path d="M1 11 L7 5" stroke="#0e9fd8" stroke-width="2.4" stroke-linecap="round"/><circle cx="8.5" cy="3.5" r="3" fill="#0e9fd8"/></svg>Support</span>
  </div>
</div>

<header class="abs header">
  <div class="abs brand"><i></i>Brenwick Structures</div>
  <nav class="abs nav">
    <a class="active">HOME</a><a>PORTFOLIO</a><a>PRODUCT SPECS</a><a>TESTIMONIALS</a><a>OUR PROCESS</a>
  </nav>
  <div class="abs contact-btn">CONTACT US</div>
</header>

<section class="abs hero" role="img" aria-label="Two engineers in hard hats reviewing plans in a bright office"></section>
<div class="abs dots"><i class="on"></i><i></i><i></i><i></i></div>

<section class="abs welcome">
  <h1>WELCOME TO <span>BRENWICK STRUCTURES</span></h1>
  <p class="intro">Sed ut perspiciatis unde omnis iste natus error sit voluptatem accusantium doloremque laudantium, totam rem aperiam, eaque ipsa quae ab illo inventore veritatis et quasi architecto beatae vitae dicta sunt explicabo. Nemo enim ipsam voluptatem quia voluptas sit aspernatur aut odit aut fugit, sed quia consequuntur magni dolores eos qui ratione voluptatem</p>
  <div class="tabs"><span class="active">RESIDENTIAL</span><span class="tab-com">COMMERCIAL</span><span class="tab-agr">AGRICULTURAL</span></div>

  <article class="card" style="left:92px">
    <div class="photo" role="img" aria-label="Stucco family home with garden under blue sky" style="background:linear-gradient(180deg,#6f9fd6 0%,#b7a98f 55%,#4d7a35 100%)"></div>
    <p>Nemo enim ipsam voluptatem quia voluptas sit aspernatur aut eos qui ratione volupta.</p>
    <div class="btn-red">LEARN MORE</div>
  </article>
  <article class="card" style="left:350px">
    <div class="photo" role="img" aria-label="Stone house with patio and lawn" style="background:linear-gradient(180deg,#cfd6dc 0%,#8c7f6e 55%,#5b8a3a 100%)"></div>
    <p>Nemo enim ipsam voluptatem quia voluptas sit aspernatur aut eos qui ratione volupta.</p>
    <div class="btn-red">LEARN MORE</div>
  </article>
  <article class="card" style="left:608px">
    <div class="photo" role="img" aria-label="Two-storey house lit at dusk" style="background:linear-gradient(180deg,#6b8fc9 0%,#9fa8b8 50%,#6a6a55 100%)"></div>
    <p>Nemo enim ipsam voluptatem quia voluptas sit aspernatur aut eos qui ratione volupta.</p>
    <div class="btn-red">LEARN MORE</div>
  </article>
  <article class="card" style="left:866px">
    <div class="photo" role="img" aria-label="Modern white house with glass walls on a lawn" style="background:linear-gradient(180deg,#4f9be0 0%,#dcdcd8 55%,#6aa043 100%)"></div>
    <p>Nemo enim ipsam voluptatem quia voluptas sit aspernatur aut eos qui ratione volupta.</p>
    <div class="btn-red">LEARN MORE</div>
  </article>
</section>

<section class="abs testimonial" role="img" aria-label="Blurred living room interior behind client testimonial">
  <svg class="abs quote-mark" width="40" height="32" viewBox="0 0 40 32"><path d="M0 32V18C0 8 5 2 14 0l2 5C10 7 8 11 8 15h8v17Zm22 0V18C22 8 27 2 36 0l2 5c-6 2-8 6-8 10h8v17Z" fill="#fff"/></svg>
  <blockquote>Sed ut perspiciatis unde omnis iste natus error sit voluptatem accusantium doloremque laudantium, totam rem aperiam, eaque ipsa quae ab illo inventore veritatis et quasi architecto beatae vitae dicta sunt explicabo. Nemo enim ipsam voluptatem quia voluptas sit aspernatur aut odit magni dolores eos qui ratione volupta.</blockquote>
  <div class="abs arrows">
    <svg width="22" height="22" viewBox="0 0 22 22"><circle cx="11" cy="11" r="10" fill="none" stroke="#fff" stroke-width="1.5"/><path d="M13 6 L8 11 L13 16" fill="none" stroke="#fff" stroke-width="2"/></svg>
    <svg width="22" height="22" viewBox="0 0 22 22"><circle cx="11" cy="11" r="10" fill="none" stroke="#fff" stroke-width="1.5"/><path d="M9 6 L14 11 L9 16" fill="none" stroke="#fff" stroke-width="2"/></svg>
  </div>
  <div class="abs avatar" role="img" aria-label="Client portrait"></div>
  <div class="abs person">ALAN REYES</div>
</section>

<h2 class="abs blog-title">BLOG POST</h2>
<article class="post" style="left:85px">
  <div class="photo" role="img" aria-label="Modern white living room with sofa and television" style="background:linear-gradient(135deg,#e8e6e2 0%,#c9c4bc 50%,#6b5a4a 100%)">
    <div class="date"><b>03</b><small>NOV 15</small></div>
  </div>
  <p>Sed ut perspiciatis unde omnis iste natus error sit voluptatem accusantium doloremque laudantium, totam rem aperiam, eaque ipsa.</p>
  <div class="btn-blue">LEARN MORE</div>
</article>
<article class="post" style="left:434px">
  <div class="photo" role="img" aria-label="White terrace lounge overlooking the sea" style="background:linear-gradient(180deg,#5aa6e6 0%,#bfdcf0 45%,#eef1f2 100%)">
    <div class="date"><b>03</b><small>NOV 15</small></div>
  </div>
  <p>Sed ut perspiciatis unde omnis iste natus error sit voluptatem accusantium doloremque laudantium, totam rem aperiam, eaque ipsa.</p>
  <div class="btn-blue">LEARN MORE</div>
</article>
<article class="post" style="left:783px">
  <div class="photo" role="img" aria-label="Bright interior with wooden folding doors and plant" style="background:linear-gradient(90deg,#dfe3e6 0%,#c9a878 50%,#eceae5 100%)">
    <div class="date"><b>03</b><small>NOV 15</small></div>
  </div>
  <p>Sed ut perspiciatis unde omnis iste natus error sit voluptatem accusantium doloremque laudantium, totam rem aperiam, eaque ipsa.</p>
  <div class="btn-blue">LEARN MORE</div>
</article>

<footer class="abs footer">
  <div class="abs footer-nav"><span>HOME</span><span>HOW WE WORK</span><span>SERVICES</span><span>ABOUT US</span><span>CONTACT US</span></div>
  <div class="abs copyright">© 2015, Yoursite, All Right Reserved.</div>
  <div class="abs socials">
    <i style="background:#3b5998"></i><i style="background:#1da1f2"></i><i style="background:#dd4b39"></i><i style="background:#3f729b"></i>
  </div>
</footer>

</body>
</html>
```